Webdesign für industrielle Produktion von Suppen, Saucen, Bouillons und Konzentraten
Zielgruppe
Industrielle Produktion von Suppen, Saucen, Bouillons und Konzentraten
Aufgabenstellung
Aufmachung nicht zu modern, eher klassisch Understatement

```html
<!DOCTYPE html>
<html lang="de">
<head>
<meta charset="utf-8">
<title>Vellmar Foodservice – Nachricht</title>
<link href="https://fonts.googleapis.com/css2?family=Outfit:wght@400;500;600;700&family=PT+Sans:wght@400;700&display=swap" rel="stylesheet">
<style>
:root{
  --red:#d8141b;
  --red-dark:#8f0c12;
  --ink:#111;
  --white:#fff;
  --blue:#1f74b4;
}
*{box-sizing:border-box;margin:0;padding:0}
html,body{width:1200px;height:2696px;overflow:hidden;background:var(--white)}
body{position:relative;font-family:"Outfit",sans-serif;color:var(--ink)}
.abs{position:absolute}
.center{left:0;width:1200px;text-align:center}

/* hero */
.hero{top:0;left:0;width:1200px;height:413px;background:radial-gradient(ellipse at 50% 40%,#c4151c 0%,#a40f15 55%,#7c0a10 100%)}
.nav-ribbon{top:50px;width:50px;height:66px;background:#e8e8e8}
.nav-ribbon.left{left:60px;clip-path:polygon(0 0,100% 0,100% 100%,0 100%,30% 50%)}
.nav-ribbon.right{left:1090px;clip-path:polygon(0 0,100% 0,70% 50%,100% 100%,0 100%)}
.nav{top:41px;left:86px;width:1028px;height:66px;background:var(--white);display:flex;align-items:center;padding:0 13px;font-size:14px;font-weight:500}
.nav a{color:var(--ink);text-decoration:none;margin-right:16px}
.nav a.active{color:var(--red)}
.nav .contact{position:absolute;left:626px}
.brand{position:absolute;left:424px;top:0;width:180px;height:66px;display:flex;align-items:center;justify-content:center;gap:8px;color:var(--red);font-size:28px;font-weight:700}
.brand i{width:14px;height:14px;background:var(--red)}
.search{position:absolute;left:735px;top:16px;width:212px;height:34px;border:1.5px solid #333;border-radius:5px;display:flex;align-items:center;justify-content:space-between;padding:0 10px 0 14px;font-size:14px}
.nav-icons{position:absolute;left:960px;top:22px;display:flex;gap:12px}
.hero-label{top:166px;color:var(--white);font-size:18px;font-weight:500}
.hero-title{top:196px;color:var(--white);font-size:63px;font-weight:700;line-height:81px}

/* headings */
.eyebrow{font-size:18px;font-weight:500}
.title{font-size:44px;font-weight:700;line-height:49px}
.title em{font-style:normal;color:var(--red)}

/* certificate */
.btn-outline{top:689px;left:60px;width:194px;height:40px;border:2px solid var(--ink);border-radius:6px;display:flex;align-items:center;justify-content:center;font-size:15px;font-weight:500}
.btn-pdf{top:683px;left:846px;width:294px;height:51px;border-radius:6px;background:linear-gradient(90deg,#d31a20,#7a0b10);color:var(--white);font-size:11px;line-height:15px;padding:10px 0 0 70px}
.pdf-doc{top:-4px;left:14px;width:50px;height:62px;background:var(--white);border:1px solid #ccc;border-radius:2px}
.pdf-doc::before{content:"";position:absolute;top:0;left:0;width:26px;height:14px;background:var(--red)}
.cert{top:785px;left:60px;width:1080px;height:280px;background:linear-gradient(90deg,#eceef0,#fafafa);font-family:"PT Sans",sans-serif;overflow:hidden}
.cert-blue{top:0;left:805px;width:275px;height:280px;background:radial-gradient(circle at 30% 30%,#2c86c6,#1b5f99)}
.cert-text{top:10px;right:353px;text-align:right}
.cert-head{font-size:50px;font-weight:700;letter-spacing:1px}
.cert-sub{font-size:23px;margin-top:-4px}
.cert-small{font-size:17px;margin-top:40px}
.cert-co{font-size:27px;font-weight:700;margin-top:30px}
.cert-addr{font-size:19px}

/* product band */
.band{top:1230px;left:0;width:1200px;height:297px;background:linear-gradient(180deg,#6a1419 0%,#4a0e12 75%,#8a6246 76%,#6d4a31 100%)}
.products{top:1145px;left:667px;width:533px;height:362px;background:linear-gradient(90deg,#b44a34 0%,#d9c28a 35%,#e8d060 65%,#f2f2ee 100%);border-radius:40px 0 0 20px}
.band-new{top:1290px;left:60px;color:var(--white);font-size:18px;font-weight:500}
.band-title{top:1321px;left:60px;color:var(--white);font-size:44px;font-weight:700;line-height:48px}

/* video */
.video{top:1773px;left:60px;width:1080px;height:412px;border-radius:10px;background:radial-gradient(ellipse at 48% 45%,#d9a24a 0%,#f2f2f2 28%,#8c8c8c 60%,#707070 100%);overflow:hidden}
.play{top:1943px;left:564px;width:72px;height:72px;border-radius:50%;background:rgba(255,255,255,.55)}

/* footer */
.footer{top:2260px;left:0;width:1200px;height:436px;background:radial-gradient(ellipse at 50% 30%,#c8161c,#8d0b11 70%,#6d080c);color:var(--white)}
.f-brand{top:78px;left:60px;display:flex;align-items:center;gap:10px;font-size:40px;font-weight:700}
.f-brand i{width:18px;height:18px;background:var(--white)}
.f-about{top:175px;left:60px;width:310px;font-size:13px;line-height:16px}
.pay{top:256px;left:60px;display:flex;gap:15px}
.pay span{width:38px;height:24px;border-radius:3px;background:var(--white)}
.f-news{top:78px;left:609px;font-size:18px;font-weight:500;line-height:22px}
.f-input{top:71px;left:819px;width:321px;height:42px;border-radius:5px;background:var(--white);color:var(--ink);font-size:14px;font-weight:500;padding:12px 0 0 26px;overflow:hidden}
.f-input i{position:absolute;right:0;top:0;width:50px;height:42px;background:var(--red);display:flex;align-items:center;justify-content:center}
.f-col h4{font-size:18px;font-weight:500;margin-bottom:14px}
.f-col p{font-size:14px;line-height:28px}
.f-rule{top:354px;left:60px;width:1080px;height:2px;background:rgba(255,255,255,.75)}
.socials{top:385px;left:60px;display:flex;gap:10px}
.socials span{width:15px;height:15px;border-radius:50%;background:var(--white)}
.copy{top:385px;right:60px;font-size:11px}
</style>
</head>
<body>

<header class="abs hero">
  <div class="abs nav-ribbon left"></div>
  <div class="abs nav-ribbon right"></div>
  <nav class="abs nav">
    <a>Geschäft</a><a>GV-Produkte</a><a>Catering-Produkte</a><a class="active">Nachricht</a>
    <div class="brand"><i></i>Vellmar</div>
    <a class="contact">Kontakt</a>
    <div class="search">Hier Suchen
      <svg width="18" height="18" viewBox="0 0 24 24" fill="none" stroke="#111" stroke-width="2.2"><circle cx="10" cy="10" r="7"/><path d="M15 15l6 6"/></svg>
    </div>
    <div class="nav-icons">
      <svg width="20" height="20" viewBox="0 0 24 24" fill="none" stroke="#111" stroke-width="2"><circle cx="12" cy="8" r="4"/><path d="M4 21c1-5 15-5 16 0"/></svg>
      <svg width="22" height="20" viewBox="0 0 24 22" fill="none" stroke="#111" stroke-width="2"><path d="M1 2h4l3 12h12l2-9H6"/><circle cx="9" cy="19" r="1.5"/><circle cx="18" cy="19" r="1.5"/></svg>
    </div>
  </nav>
  <p class="abs center hero-label">Catering Products</p>
  <h1 class="abs center hero-title">Perfekte Zutaten Für<br>Unvergessliche Ereignisse</h1>
</header>

<p class="abs center eyebrow" style="top:520px">Vellmar, An Energy-Certified Company</p>
<h2 class="abs center title" style="top:551px"><em>Nachhaltigkeit</em> Mit Zertifizierter<br>Expertise Fördern</h2>

<div class="abs btn-outline">View Full Screen</div>
<div class="abs btn-pdf"><div class="abs pdf-doc"></div>Laden Sie Vellmar An Energy Herunter<br>Zertifiziertes Unternehmen</div>

<section class="abs cert">
  <div class="abs cert-blue"></div>
  <div class="abs cert-text">
    <div class="cert-head">ZERTIFIKAT</div>
    <div class="cert-sub">Energetisch geprüftes Unternehmen</div>
    <div class="cert-small">Das Unternehmen</div>
    <div class="cert-co">Brenner GmbH &amp; Co. KG</div>
    <div class="cert-addr">Lindenallee 12 | 40210 Musterstadt | DE</div>
  </div>
</section>

<section>
  <div class="abs band"></div>
  <div class="abs products" role="img" aria-label="Drei Konservendosen mit Ochsenschwanzsuppe, Rindbouillon und Rinder-Fond"></div>
  <p class="abs band-new">!!New!!</p>
  <h2 class="abs band-title">Feine Verzehrfertige<br>Suppenspezialitäten Aus<br>Erlesenen Zutaten</h2>
</section>

<p class="abs center eyebrow" style="top:1599px">Hilfstransport Für Die Ukraine</p>
<h2 class="abs center title" style="top:1631px"><em>Den Humanitären</em> Bedürfnissen<br>Der <em>Ukraine</em> Gewidmet</h2>

<div class="abs video" role="img" aria-label="Videovorschau: Teller mit Gemüsesuppe und Löffel"></div>
<div class="abs play"><svg width="72" height="72" viewBox="0 0 72 72"><path d="M29 22l22 14-22 14z" fill="#fff"/></svg></div>

<footer class="abs footer">
  <div class="abs f-brand"><i></i>Vellmar</div>
  <p class="abs f-about">Lorem Ipsum Dolor Sit Amet Consectetur. Ut Nulla Pellentesque Turpis Viverra Id Amet Bibendum.</p>
  <div class="abs pay"><span></span><span></span><span></span><span></span><span></span></div>
  <p class="abs f-news">Abonnieren Sie<br>Unseren Neuen Brief</p>
  <div class="abs f-input">Enter Your Email<i><svg width="14" height="14" viewBox="0 0 14 14" fill="none" stroke="#fff" stroke-width="2"><path d="M4 1l6 6-6 6"/></svg></i></div>
  <div class="abs f-col" style="top:143px;left:609px"><h4>Company</h4><p>About Us<br>Work With Us<br>Blog &amp; News</p></div>
  <div class="abs f-col" style="top:143px;left:842px"><h4>Shop</h4><p>Collections<br>Blog Post<br>Wishlist</p></div>
  <div class="abs f-col" style="top:143px;left:1055px"><h4>Quick Link</h4><p>Shop<br>Products<br>Contact</p></div>
  <div class="abs f-rule"></div>
  <div class="abs socials"><span></span><span></span><span></span><span></span></div>
  <p class="abs copy">Copyright © 2024 <b>STUDIO NORDEN</b>. All Rights Reserved.</p>
</footer>

</body>
</html>
```